New Bicycle shop business card

Hi!
I'm looking for a business card for my new proffesional bike mechanics shop. This shop is only for fixing broken bikes and not selling bikes.
Peferbly a modern and sleek and modern design.
Colors: black, grey, red, white
Information:
Name: Rijwielwerkplaats Vanhoutte
Shop owner: Bart Vanhoutte & Marieke Segers
Website: www.rijwielwerkplaats-vanhoutte.be
Email: info@rijwielwerkplaats-vanhoutte.be
Phone number: +32471902368
Street adres: Kerkweg 46
9940 Bellebeke
Slogan/shop information: Herstellingen van alle merken.
Logo: see files.
Target Market(s)
People who seek a mechanic to fix or upgrade their bikes.
Contact Information for Business Card
Information:
Website: info@rijwielwerkplaats-vanhoutte.be
9940 Bellebeke
Logo: see files.

```html
<!DOCTYPE html>
<html lang="nl">
<head>
<meta charset="utf-8">
<title>Rijwielwerkplaats Vanhoutte – visitekaartje</title>
<link href="https://fonts.googleapis.com/css2?family=Lato:wght@400;700;900&display=swap" rel="stylesheet">
<style>
  :root {
    --stage: #2f2f31;
    --red: #e0133d;
    --red-deep: #c90f35;
    --red-soft: rgba(255,255,255,0.08);
    --ink: #1b1b1b;
    --grey: #6b6b6b;
    --rule: #bdbdbd;
    --paper: #ffffff;
    --ghost: #ededed;
  }
  * { margin: 0; padding: 0; box-sizing: border-box; }
  html, body {
    width: 1200px; height: 866px; overflow: hidden;
    background: var(--stage);
    font-family: "Lato", sans-serif;
  }
  .stage {
    width: 1200px; height: 866px;
    display: flex; flex-direction: column; align-items: center; justify-content: center;
    gap: 48px;
  }
  .card {
    position: relative; width: 620px; height: 354px; overflow: hidden;
    box-shadow: 0 10px 24px rgba(0,0,0,0.45);
  }

  /* front */
  .card-front { background: var(--paper); border-bottom: 12px solid var(--red); }
  .card-front .ghost-mark {
    position: absolute; left: 120px; top: -60px; width: 330px; height: 330px;
    border-radius: 50%; background: var(--ghost);
  }
  .contact {
    position: absolute; left: 40px; top: 92px; width: 300px;
  }
  .contact .owners {
    color: var(--red); font-weight: 700; font-size: 15px; text-transform: uppercase; letter-spacing: 0.2px;
  }
  .contact .role { color: var(--grey); font-size: 14px; margin: 2px 0 12px; }
  .contact ul { list-style: none; }
  .contact li {
    display: flex; align-items: center; gap: 8px;
    color: var(--ink); font-size: 13px; line-height: 21px;
  }
  .contact svg { width: 12px; height: 12px; flex: none; fill: var(--red); }
  .brand {
    position: absolute; right: 40px; top: 96px; text-align: left;
    display: flex; align-items: center; gap: 12px;
  }
  .brand-dot { width: 34px; height: 34px; border-radius: 50%; background: var(--red); flex: none; }
  .brand-name {
    color: var(--ink); font-weight: 900; font-size: 17px; line-height: 1.3;
    text-transform: uppercase; letter-spacing: 1px;
  }
  .brand-name .second { display: block; letter-spacing: 9px; }
  .divider {
    position: absolute; left: 300px; right: 40px; top: 196px;
    height: 1px; background: var(--rule);
  }
  .address {
    position: absolute; right: 40px; top: 214px; text-align: right;
    color: var(--ink); font-size: 15px; line-height: 22px; letter-spacing: 0.5px;
  }

  /* back */
  .card-back { background: var(--red); }
  .card-back .ghost-mark {
    position: absolute; left: 150px; top: -40px; width: 320px; height: 320px;
    border-radius: 50%; background: var(--red-soft);
  }
  .back-title {
    position: absolute; inset: 0;
    display: flex; flex-direction: column; align-items: center; justify-content: center;
    color: var(--paper); text-align: center;
  }
  .back-title .name {
    font-weight: 900; font-size: 26px; line-height: 1.3; letter-spacing: 1.5px; text-transform: uppercase;
  }
  .back-title .name .second { display: block; letter-spacing: 12px; }
  .back-title .slogan {
    margin-top: 10px; font-size: 14px; letter-spacing: 0.5px; text-transform: uppercase;
  }
</style>
</head>
<body>
<main class="stage">
  <section class="card card-front" aria-label="Voorkant visitekaartje">
    <div class="ghost-mark" aria-hidden="true"></div>
    <div class="contact">
      <p class="owners">Bart Vanhoutte &amp; Marieke Segers</p>
      <p class="role">Owner</p>
      <ul>
        <li><svg viewBox="0 0 12 12" aria-hidden="true"><path d="M2.5 0.8 4.4 3.2 3.3 4.6c.7 1.5 2 2.9 3.6 3.7l1.3-1.1 2.4 1.8-.9 2.1C5.3 11 1 6.7.8 2z"/></svg>+32471902368</li>
        <li><svg viewBox="0 0 12 12" aria-hidden="true"><path d="M0 2h12v8H0zM1 3v.4l5 3.2 5-3.2V3z" fill-rule="evenodd"/></svg>info@rijwielwerkplaats-vanhoutte.be</li>
        <li><svg viewBox="0 0 12 12" aria-hidden="true"><circle cx="6" cy="6" r="5.5"/><path d="M1 6h10M6 .5c-2.4 3-2.4 8 0 11M6 .5c2.4 3 2.4 8 0 11" stroke="#fff" stroke-width=".8" fill="none"/></svg>www.rijwielwerkplaats-vanhoutte.be</li>
      </ul>
    </div>
    <div class="brand">
      <span class="brand-dot" aria-hidden="true"></span>
      <p class="brand-name">Rijwielwerkplaats <span class="second">Vanhoutte</span></p>
    </div>
    <div class="divider" aria-hidden="true"></div>
    <address class="address" style="font-style:normal">Kerkweg 46<br>9940 Bellebeke</address>
  </section>

  <section class="card card-back" aria-label="Achterkant visitekaartje">
    <div class="ghost-mark" aria-hidden="true"></div>
    <div class="back-title">
      <p class="name">Rijwielwerkplaats <span class="second">Vanhoutte</span></p>
      <p class="slogan">Herstellingen van alle merken</p>
    </div>
  </section>
</main>
</body>
</html>
```